Birch And Harbor Website A Website design for book editing

A website design for book editing

Our proofreading, editing and manuscript review packages are specifically tailored to help you publish the best possible version of your story.

NEED HELP PUBLISHING A BESTSELLER?

If you’re looking for professional book editing services from senior publishing industry insiders, look no further. Besides editing, we can also answer all your publishing questions and get you started building your author platform.

OUR SERVICES

We've carefully structured our packages to maximize value for every budget.

PRICING

$.02
PER WORD
Proofreading
Line Edit (Copy-editing)
Fix spelling and grammar
Sales copy/summary revision

$.04
PER WORD
Proofreading
Line Edit (Copy-editing)
Fix spelling and grammar
Organization and content
Plot and pacing
Manuscript Review

$.06
PER WORD
Proofreading
Line Edit (Copy-editing)
Fix spelling and grammar
Organization and content
Plot and pacing
Manuscript Review
Formatting (print and ebook)
Pre-publication proofread

OUR PROCESS

Send us a sample of your book. Our caffeine-fueled, eagle-eyed editors will go through it and then email you with their comments and suggestions. You can ask them any questions you want. They will look for…

Typos and grammatical errors.
Spelling and word choice issues
Punctuation and style
Word choice, clarity and flow.
Sentence structure and craft
If your writing is already clean, then they’ll discuss bigger picture things with you, like theme, concept, purpose, audience, potential market and branding (including title, subtitle, and tagline or elevator pitch).

Once you feel comfortable and confident in an editor’s expertise, skill and knowledge, and are ready to move ahead, we’ll send an invoice for the first half of the total word count so the editor can get started. We’ll charge the rest when the project is close to completion.

Target Market(s)

Authors

Industry/Entity Type

Book Publisher

Coding

Coded - Design and coding required

Number of Pages Required

1 page

Requirements
Must have
• OUR SERVICES
• We've carefully structured our packages to maximize value for every budget.
• PRICING
• $.02
• PER WORD
• Proofreading
• Line Edit (Copy-editing)
• Fix spelling and grammar
• Sales copy/summary revision
• $.04
• PER WORD
• Proofreading
• Organization and content
• Plot and pacing
• Manuscript Review
• $.06
• PER WORD
• Proofreading
• Plot and pacing
• Manuscript Review
• Formatting (print and ebook)
• Pre-publication proofread

```html
<!DOCTYPE html>
<html lang="en">
<head>
<meta charset="utf-8">
<title>Birch And Harbor – Book Editing</title>
<link href="https://fonts.googleapis.com/css2?family=Jost:wght@400;500;600;700&family=Open+Sans:wght@400;600;700&display=swap" rel="stylesheet">
<style>
:root{
  --red:#e1192d;
  --red-dark:#b3101f;
  --ink:#222226;
  --text:#6b6b70;
  --line:#e6e6e6;
  --white:#ffffff;
  --black:#111113;
  --grey-bg:#f3f3f4;
}
*{margin:0;padding:0;box-sizing:border-box}
html,body{width:1200px;height:4444px;overflow:hidden}
body{position:relative;background:var(--white);font-family:"Open Sans",Arial,sans-serif;color:var(--text)}
.abs{position:absolute}
h1,h2,h3{font-family:"Jost",Arial,sans-serif}

/* header */
.site-header{left:0;top:0;width:1200px;height:100px;background:var(--white)}
.brand{left:100px;top:34px;display:flex;align-items:center;gap:10px;font-family:"Jost",sans-serif;font-weight:600;font-size:26px;color:var(--ink)}
.brand-dot{width:14px;height:14px;border-radius:50%;background:var(--red)}
.main-nav{left:430px;top:40px;display:flex;gap:40px;font-family:"Jost",sans-serif;font-size:15px;font-weight:500;color:var(--ink)}
.main-nav .active{border-bottom:2px solid var(--red);padding-bottom:4px}
.search-icon{left:1086px;top:40px}

/* hero */
.hero{left:0;top:100px;width:1200px;height:660px;background:linear-gradient(120deg,#3a3330 0%,#5c4d44 40%,#2d2927 75%,#1b1918 100%)}
.hero-title{left:0;top:326px;width:1200px;text-align:center;color:var(--white);font-family:"Jost",sans-serif;font-weight:700;font-size:38px;letter-spacing:.5px}
.hero-sub{left:0;top:384px;width:1200px;text-align:center;color:#e8e8e8;font-size:15px}
.btn{display:inline-flex;align-items:center;justify-content:center;border-radius:22px;font-family:"Jost",sans-serif;font-weight:600;font-size:13px;letter-spacing:.5px;height:42px}
.btn-red{background:var(--red);color:var(--white)}
.btn-ghost{border:2px solid var(--white);color:var(--white)}
.btn-outline{border:2px solid var(--red);color:var(--ink);background:var(--white)}
.hero-btns{left:0;top:450px;width:1200px;display:flex;justify-content:center;gap:20px}
.hero-btns .btn{width:130px}
.slider-arrow{width:40px;height:40px;border-radius:50%;background:rgba(255,255,255,.25);top:402px;display:flex;align-items:center;justify-content:center}
.hero-curve{left:0;top:560px}

/* about */
.about-title{left:100px;top:930px;font-size:44px;font-weight:600;color:var(--ink);line-height:1.1}
.about-title span{display:block;color:var(--red)}
.about-text{left:100px;top:1060px;width:440px;font-size:14px;line-height:1.75;display:flex;flex-direction:column;align-items:flex-start}
.about-text p{margin-bottom:14px}
.about-btn{width:120px;margin-top:12px}
.about-frame{left:650px;top:940px;width:450px;height:420px;border:3px solid var(--red)}
.about-photo{left:620px;top:915px;width:450px;height:410px;background:linear-gradient(135deg,#cfd3d6,#9aa1a6 55%,#6f767b)}

/* services */
.services-band{left:0;top:1480px;width:1200px;height:300px;background:linear-gradient(110deg,#d4172a 0%,#e52a3b 45%,#b80f20 100%)}
.section-title{width:1200px;left:0;text-align:center;font-size:46px;font-weight:600;color:var(--ink)}
.services-title{top:1568px;color:var(--white)}
.services-sub{left:0;top:1640px;width:1200px;text-align:center;color:#ffe6e8;font-size:15px}
.service{top:1730px;width:300px;text-align:center}
.service-icon{width:110px;height:110px;border-radius:50%;background:var(--ink);border:6px solid var(--white);box-shadow:0 0 0 3px var(--red);margin:0 auto;display:flex;align-items:center;justify-content:center}
.service h3{margin-top:34px;font-size:16px;font-weight:600;color:var(--ink);letter-spacing:.5px}
.service p{margin-top:12px;font-size:12px;line-height:1.7}
.service .btn{margin-top:26px;width:110px;height:36px}

/* pricing */
.pricing-title{top:2280px}
.pricing-sub{left:0;top:2350px;width:1200px;text-align:center;font-size:14px}
.plan{background:var(--white);border:1px solid var(--line)}
.plan-head{height:60px;background:var(--ink);color:var(--white);display:flex;align-items:center;justify-content:center;gap:6px;font-family:"Jost",sans-serif;font-size:20px;font-weight:500}
.plan-head b{color:var(--red);font-weight:600;font-size:24px}
.plan ul{list-style:none;padding:8px 18px}
.plan li{font-size:12px;color:var(--ink);height:29px;display:flex;align-items:center;gap:9px;border-bottom:1px solid var(--line);white-space:nowrap}
.plan li::before{content:"";width:6px;height:6px;border-radius:50%;background:var(--red);flex:none}
.plan-btn{position:absolute;left:0;bottom:0;width:100%;height:40px;background:var(--ink);color:var(--white);display:flex;align-items:center;justify-content:center;font-family:"Jost",sans-serif;font-weight:600;font-size:14px}
.plan-featured{box-shadow:0 10px 30px rgba(0,0,0,.18);z-index:2}
.plan-featured .plan-head{height:84px;background:var(--red)}
.plan-featured .plan-head b{color:var(--white);font-size:30px}
.plan-featured .plan-btn{background:var(--red);height:46px}

/* process */
.process-bg{left:0;top:2860px;width:1200px;height:1100px;background:linear-gradient(180deg,#f7f7f8 0%,#ececee 60%,#dcdcdf 100%)}
.process-title{top:2960px}
.process-text{left:200px;width:800px;text-align:center;font-size:13px;line-height:1.8}
.process-btn{left:535px;top:3720px;width:130px;height:40px}
.step-label{width:130px;text-align:center;font-size:12px;line-height:1.5;color:var(--ink);top:3540px}

/* footer */
.footer-curve{left:0;top:3880px}
.site-footer{left:0;top:3990px;width:1200px;height:454px;background:var(--black);color:#bdbdc2}
.footer-brand{left:100px;top:4070px;color:var(--white)}
.socials{left:100px;top:4130px;display:flex;gap:10px}
.socials span{width:26px;height:26px;border-radius:50%;background:var(--red)}
.footer-col{color:#bdbdc2}
.footer-col h3{color:var(--white);font-size:16px;font-weight:600;letter-spacing:.5px;margin-bottom:20px}
.contact-row{display:flex;gap:14px;font-size:12px;line-height:1.6;margin-bottom:16px;align-items:flex-start}
.contact-row i{width:26px;height:26px;border-radius:50%;border:1px solid #55555b;flex:none;display:flex;align-items:center;justify-content:center}
.news-input{width:320px;height:38px;border-radius:20px;background:var(--white);margin-top:18px}
.news-btn{margin-top:14px;width:110px;height:36px}
.footer-bottom{left:0;top:4370px;width:1200px;border-top:1px solid #2b2b2f;padding-top:24px;text-align:center;font-size:12px;color:#bdbdc2}
</style>
</head>
<body>

<header class="site-header abs">
  <div class="brand abs"><span class="brand-dot"></span>Birch And Harbor</div>
  <nav class="main-nav abs">
    <span class="active">Home</span><span>About us</span><span>Services</span><span>Pricing</span><span>Process</span><span>Contact us</span>
  </nav>
  <svg class="search-icon abs" width="18" height="18" viewBox="0 0 18 18"><circle cx="7.5" cy="7.5" r="5.5" fill="none" stroke="#e1192d" stroke-width="2"/><line x1="11.5" y1="11.5" x2="16.5" y2="16.5" stroke="#e1192d" stroke-width="2.2" stroke-linecap="round"/></svg>
</header>

<section class="hero abs" role="img" aria-label="Photo of hands typing on a laptop beside stacked books"></section>
<h1 class="hero-title abs">NEED HELP PUBLISHING A BESTSELLER?</h1>
<p class="hero-sub abs">Professional book editing from senior publishing industry insiders.</p>
<div class="hero-btns abs"><span class="btn btn-red">READ MORE</span><span class="btn btn-ghost">GET STARTED</span></div>
<div class="slider-arrow abs" style="left:20px"><svg width="10" height="14"><path d="M8 1 2 7l6 6" fill="none" stroke="#fff" stroke-width="2"/></svg></div>
<div class="slider-arrow abs" style="left:1140px"><svg width="10" height="14"><path d="M2 1l6 6-6 6" fill="none" stroke="#fff" stroke-width="2"/></svg></div>
<svg class="hero-curve abs" width="1200" height="220" viewBox="0 0 1200 220">
  <path d="M0 70 Q300 150 555 130 L600 70 L645 130 Q900 150 1200 70 L1200 220 L0 220 Z" fill="#fff"/>
  <path d="M0 70 Q300 150 555 130 L600 70 L645 130 Q900 150 1200 70" fill="none" stroke="#e1192d" stroke-width="4"/>
  <circle cx="600" cy="128" r="9" fill="#e1192d"/>
</svg>

<section class="about">
  <h2 class="about-title abs">About<span>Birch And Harbor</span></h2>
  <div class="about-text abs">
    <p>Our proofreading, editing and manuscript review packages are specifically tailored to help you publish the best possible version of your story.</p>
    <p>If you’re looking for professional book editing services from senior publishing industry insiders, look no further. Besides editing, we can also answer all your publishing questions.</p>
    <p>We can get you started building your author platform today.</p>
    <span class="about-btn btn btn-outline">READ MORE</span>
  </div>
  <div class="about-frame abs"></div>
  <div class="about-photo abs" role="img" aria-label="Photo of an editor reviewing printed pages at a desk"></div>
</section>

<section class="services">
  <div class="services-band abs" role="img" aria-label="Red-tinted photo of a person writing in a notebook"></div>
  <h2 class="section-title services-title abs">Our Services</h2>
  <p class="services-sub abs">We've carefully structured our packages to maximize value for every budget.</p>
  <div class="service abs" style="left:90px">
    <div class="service-icon"><svg width="44" height="44" viewBox="0 0 44 44"><rect x="8" y="5" width="22" height="30" rx="2" fill="none" stroke="#fff" stroke-width="2.5"/><circle cx="27" cy="26" r="8" fill="#222226" stroke="#fff" stroke-width="2.5"/><line x1="33" y1="32" x2="39" y2="38" stroke="#fff" stroke-width="3" stroke-linecap="round"/></svg></div>
    <h3>PROOFREADING</h3>
    <p>We catch every typo, misplaced comma<br>and stray error so your pages read<br>clean from the first line to the last.</p>
    <span class="btn btn-outline">Read More</span>
  </div>
  <div class="service abs" style="left:450px">
    <div class="service-icon"><svg width="44" height="44" viewBox="0 0 44 44"><rect x="6" y="8" width="26" height="30" rx="2" fill="none" stroke="#fff" stroke-width="2.5"/><path d="M20 30 36 10l4 3-16 20-6 2z" fill="#fff"/></svg></div>
    <h3>EDITING</h3>
    <p>Line and copy editing that sharpens<br>your sentences, tightens your prose<br>and keeps your voice intact.</p>
    <span class="btn btn-outline">Read More</span>
  </div>
  <div class="service abs" style="left:810px">
    <div class="service-icon"><svg width="44" height="44" viewBox="0 0 44 44"><path d="M10 5h18l8 8v26H10z" fill="none" stroke="#fff" stroke-width="2.5"/><line x1="15" y1="20" x2="31" y2="20" stroke="#fff" stroke-width="2.5"/><line x1="15" y1="26" x2="31" y2="26" stroke="#fff" stroke-width="2.5"/><line x1="15" y1="32" x2="26" y2="32" stroke="#fff" stroke-width="2.5"/></svg></div>
    <h3>MANUSCRIPT REVIEW PACKAGES</h3>
    <p>A full read of your manuscript with<br>notes on plot, pacing, structure and<br>character for your next draft.</p>
    <span class="btn btn-outline">Read More</span>
  </div>
</section>

<section class="pricing">
  <h2 class="section-title pricing-title abs">Our Pricing</h2>
  <p class="pricing-sub abs">Clear per-word rates for every stage of your book.</p>

  <div class="plan abs" style="left:228px;top:2448px;width:234px;height:352px">
    <div class="plan-head"><b>$.02</b>PER WORD</div>
    <ul><li>Proofreading</li><li>Line Edit (Copy-editing)</li><li>Fix spelling and grammar</li><li>Sales copy/summary revision</li></ul>
    <div class="plan-btn">VIEW MORE</div>
  </div>
  <div class="plan plan-featured abs" style="left:460px;top:2420px;width:280px;height:410px">
    <div class="plan-head"><b>$.04</b>PER WORD</div>
    <ul><li>Proofreading</li><li>Line Edit (Copy-editing)</li><li>Fix spelling and grammar</li><li>Organization and content</li><li>Plot and pacing</li><li>Manuscript Review</li></ul>
    <div class="plan-btn">VIEW MORE</div>
  </div>
  <div class="plan abs" style="left:738px;top:2448px;width:234px;height:352px">
    <div class="plan-head"><b>$.06</b>PER WORD</div>
    <ul><li>Proofreading</li><li>Line Edit (Copy-editing)</li><li>Fix spelling and grammar</li><li>Organization and content</li><li>Plot and pacing</li><li>Manuscript Review</li><li>Formatting (print and ebook)</li><li>Pre-publication proofread</li></ul>
    <div class="plan-btn">VIEW MORE</div>
  </div>
</section>

<section class="process">
  <div class="process-bg abs" role="img" aria-label="Faded photo of an open book and coffee on a desk"></div>
  <h2 class="section-title process-title abs">Our Process</h2>
  <p class="process-text abs" style="top:3040px">Send us a sample of your book. Our caffeine-fueled, eagle-eyed editors will go through it and then email you with their comments and suggestions. You can ask them any questions you want. They will look for…</p>
  <svg class="abs" style="left:0;top:3240px" width="1200" height="300" viewBox="0 0 1200 300">
    <line x1="180" y1="270" x2="1020" y2="270" stroke="#c9c9cc" stroke-width="2"/>
    <g>
      <line x1="332" y1="150" x2="332" y2="270" stroke="#f2a623" stroke-width="2"/><circle cx="332" cy="270" r="6" fill="#f2a623"/>
      <circle cx="332" cy="120" r="36" fill="#fff" stroke="#f2a623" stroke-width="8"/><circle cx="332" cy="120" r="24" fill="#eee"/>
      <text x="332" y="128" text-anchor="middle" font-family="Jost,sans-serif" font-size="22" font-weight="600" fill="#222226">1</text>
    </g>
    <g>
      <line x1="472" y1="90" x2="472" y2="270" stroke="#e1192d" stroke-width="2"/><circle cx="472" cy="270" r="6" fill="#e1192d"/>
      <circle cx="472" cy="60" r="36" fill="#fff" stroke="#e1192d" stroke-width="8"/><circle cx="472" cy="60" r="24" fill="#eee"/>
      <text x="472" y="68" text-anchor="middle" font-family="Jost,sans-serif" font-size="22" font-weight="600" fill="#222226">2</text>
    </g>
    <g>
      <line x1="600" y1="150" x2="600" y2="270" stroke="#d8204f" stroke-width="2"/><circle cx="600" cy="270" r="6" fill="#d8204f"/>
      <circle cx="600" cy="120" r="36" fill="#fff" stroke="#d8204f" stroke-width="8"/><circle cx="600" cy="120" r="24" fill="#eee"/>
      <text x="600" y="128" text-anchor="middle" font-family="Jost,sans-serif" font-size="22" font-weight="600" fill="#222226">3</text>
    </g>
    <g>
      <line x1="732" y1="90" x2="732" y2="270" stroke="#7b3fb4" stroke-width="2"/><circle cx="732" cy="270" r="6" fill="#7b3fb4"/>
      <circle cx="732" cy="60" r="36" fill="#fff" stroke="#7b3fb4" stroke-width="8"/><circle cx="732" cy="60" r="24" fill="#eee"/>
      <text x="732" y="68" text-anchor="middle" font-family="Jost,sans-serif" font-size="22" font-weight="600" fill="#222226">4</text>
    </g>
    <g>
      <line x1="860" y1="150" x2="860" y2="270" stroke="#2c7be0" stroke-width="2"/><circle cx="860" cy="270" r="6" fill="#2c7be0"/>
      <circle cx="860" cy="120" r="36" fill="#fff" stroke="#2c7be0" stroke-width="8"/><circle cx="860" cy="120" r="24" fill="#eee"/>
      <text x="860" y="128" text-anchor="middle" font-family="Jost,sans-serif" font-size="22" font-weight="600" fill="#222226">5</text>
    </g>
  </svg>
  <p class="step-label abs" style="left:267px">Typos and<br>grammatical errors</p>
  <p class="step-label abs" style="left:407px">Spelling and<br>word choice issues</p>
  <p class="step-label abs" style="left:535px">Punctuation<br>and style</p>
  <p class="step-label abs" style="left:667px">Word choice,<br>clarity and flow</p>
  <p class="step-label abs" style="left:795px">Sentence structure<br>and craft</p>
  <p class="process-text abs" style="top:3630px">If your writing is already clean, then they’ll discuss bigger picture things with you, like theme, concept, purpose, audience, potential market and branding (including title, subtitle, and tagline or elevator pitch).</p>
  <span class="process-btn abs btn btn-outline">READ MORE</span>
</section>

<svg class="footer-curve abs" width="1200" height="112" viewBox="0 0 1200 112">
  <path d="M0 40 Q300 120 555 100 L600 40 L645 100 Q900 120 1200 40 L1200 112 L0 112 Z" fill="#111113"/>
  <circle cx="600" cy="90" r="9" fill="#e1192d"/>
</svg>
<footer class="site-footer abs"></footer>
<div class="brand footer-brand abs"><span class="brand-dot"></span>Birch And Harbor</div>
<div class="socials abs"><span></span><span></span><span></span><span></span><span></span></div>
<div class="footer-col abs" style="left:392px;top:4070px;width:300px">
  <h3>CONTACT US</h3>
  <div class="contact-row"><i><svg width="10" height="14" viewBox="0 0 10 14"><path d="M5 13S1 8 1 5a4 4 0 0 1 8 0c0 3-4 8-4 8z" fill="#e1192d"/></svg></i><span>24 Harbor Lane, Suite 5<br>Birchwood, ST 00000</span></div>
  <div class="contact-row"><i><svg width="12" height="12" viewBox="0 0 12 12"><path d="M2 1h2l1 3-1.5 1a7 7 0 0 0 3.5 3.5L8 7l3 1v2a1 1 0 0 1-1 1A9 9 0 0 1 1 2a1 1 0 0 1 1-1z" fill="#e1192d"/></svg></i><span>Phone : 1 555 010 2040</span></div>
</div>
<div class="footer-col abs" style="left:768px;top:4070px;width:340px">
  <h3>SIGN UP NEWSLETTER</h3>
  <p style="font-size:12px">Get editing tips and publishing news in your inbox.</p>
  <div class="news-input"></div>
  <span class="btn btn-red news-btn">SUBSCRIBE</span>
</div>
<div class="footer-bottom abs">© copyright 2024 Birch And Harbor All Rights Reserved | Privacy policy</div>

</body>
</html>
```